wealth management firm, professional group, new model

we have a logo that works but we need a card, white background using our colors...clean look

our tag line if can be used in

The Bridge From Client to Owner

```html
<!DOCTYPE html>
<html lang="en">
<head>
<meta charset="utf-8">
<title>Arvela Wealth Partners – Business Card</title>
<link rel="stylesheet" href="https://fonts.googleapis.com/css2?family=Montserrat:wght@400&family=Nunito:wght@400;800&display=swap">
<style>
  :root {
    --navy: #172c4f;
    --ink: #111827;
    --paper: #ffffff;
    --backdrop: #d6d6d6;
  }
  * { box-sizing: border-box; margin: 0; padding: 0; }
  html, body { width: 1200px; height: 1018px; overflow: hidden; }
  body {
    background: var(--backdrop);
    display: flex;
    flex-direction: column;
    align-items: center;
    justify-content: center;
    gap: 80px;
    font-family: "Nunito", sans-serif;
  }
  .card {
    position: relative;
    width: 620px;
    height: 354px;
    box-shadow: 0 6px 18px rgba(0,0,0,0.18);
  }
  .card__frame {
    position: absolute;
    inset: 20px;
    border: 2px solid var(--navy);
  }
  .card--front { background: var(--paper); }
  .card--back { background: var(--navy); }
  .card--back .card__frame { border-color: var(--paper); }

  .wordmark {
    position: absolute;
    left: 0; right: 0;
    text-align: center;
    font-family: "Montserrat", sans-serif;
    font-weight: 400;
    color: var(--navy);
  }
  .wordmark__name { display: block; letter-spacing: 0.42em; padding-left: 0.42em; }
  .wordmark__line { display: block; letter-spacing: 0.22em; padding-left: 0.22em; }

  .card--front .wordmark { top: 48px; }
  .card--front .wordmark__name { font-size: 44px; line-height: 1; }
  .card--front .wordmark__line { font-size: 15px; margin-top: 8px; }

  .card--back .wordmark { top: 108px; color: var(--paper); }
  .card--back .wordmark__name { font-size: 64px; line-height: 1; }
  .card--back .wordmark__line { font-size: 20px; margin-top: 12px; }

  .person {
    position: absolute;
    left: 48px;
    top: 170px;
    color: var(--navy);
  }
  .person__name { font-weight: 800; font-size: 27px; line-height: 1.05; letter-spacing: 0.01em; }
  .person__role { font-size: 15px; color: var(--ink); margin-top: 2px; }

  .divider {
    position: absolute;
    left: 300px;
    top: 168px;
    width: 1.5px;
    height: 64px;
    background: var(--navy);
  }

  .contacts {
    position: absolute;
    left: 322px;
    top: 166px;
    list-style: none;
    font-size: 15.5px;
    color: var(--ink);
    line-height: 23px;
  }
  .contacts li, .address { display: flex; align-items: center; gap: 8px; }
  .icon { width: 12px; height: 12px; fill: var(--navy); flex: none; }

  .address {
    position: absolute;
    left: 48px;
    top: 258px;
    font-size: 15.5px;
    color: var(--ink);
  }
</style>
</head>
<body>
  <section class="card card--front" aria-label="Card front">
    <div class="card__frame"></div>
    <div class="wordmark">
      <span class="wordmark__name">ARVELA</span>
      <span class="wordmark__line">WEALTH PARTNERS</span>
    </div>
    <div class="person">
      <p class="person__name">DANA WHITLOW</p>
      <p class="person__role">Managing Director/CEO</p>
    </div>
    <div class="divider"></div>
    <ul class="contacts">
      <li><svg class="icon" viewBox="0 0 24 24"><path d="M6.6 10.8a15.1 15.1 0 0 0 6.6 6.6l2.2-2.2a1 1 0 0 1 1-.25 11.4 11.4 0 0 0 3.6.57 1 1 0 0 1 1 1V20a1 1 0 0 1-1 1A17 17 0 0 1 3 4a1 1 0 0 1 1-1h3.5a1 1 0 0 1 1 1c0 1.25.2 2.45.57 3.57a1 1 0 0 1-.25 1z"/></svg>+010 555 0147</li>
      <li><svg class="icon" viewBox="0 0 24 24"><path d="M2 5h20v14H2z M2 5l10 8 10-8" fill="none" stroke="#172c4f" stroke-width="2.5"/></svg>hello@arvelawealth.com</li>
      <li><svg class="icon" viewBox="0 0 24 24"><circle cx="12" cy="12" r="10"/></svg>www.arvelawealth.com</li>
    </ul>
    <p class="address"><svg class="icon" viewBox="0 0 24 24"><path d="M12 2a7 7 0 0 0-7 7c0 5.2 7 13 7 13s7-7.8 7-13a7 7 0 0 0-7-7zm0 9.5A2.5 2.5 0 1 1 12 6.5a2.5 2.5 0 0 1 0 5z"/></svg>48 Harbour Lane, Eastport - 4410</p>
  </section>

  <section class="card card--back" aria-label="Card back">
    <div class="card__frame"></div>
    <div class="wordmark">
      <span class="wordmark__name">ARVELA</span>
      <span class="wordmark__line">WEALTH PARTNERS</span>
    </div>
  </section>
</body>
</html>
```